Business Card Design & Gift cards, Gift Cert, Donation Card

Retail Gift Store-in addition to Business Cards we'd like sequenced 2 sided Gift cards, Gift Certificate Cards, and Donation Cards.please see examples and email for clarificationlogos attached with examples-
Gift Card, Gift Certificate and Donation Card will all be same style just differant upper right title, with back side info as example.
business card, as example is single sided.
looking for additional ideas for layout

Industry/Entity Type

Business

Contact Information for Business Card

211 Newman St.East Tawas, MI 48730989.362.8730Office@BrewKrew.com

Requirements
Must have
• Blue as per example
• Logos provided
• like gradiant background

```html
<!DOCTYPE html>
<html lang="en">
<head>
<meta charset="utf-8">
<title>Tillow Marsh — Business Card &amp; Gift Card</title>
<link rel="stylesheet" href="https://fonts.googleapis.com/css2?family=Comic+Neue:wght@400;700&display=swap">
<style>
  :root {
    --backdrop: #3b3b3b;
    --card: #ffffff;
    --band: #000000;
    --ink: #111111;
    --rule: #333333;
    --on-band: #ffffff;
    --art-blue: #e3e8fb;
    --art-sun: #fbf3cf;
  }
  * { box-sizing: border-box; margin: 0; padding: 0; }
  html, body {
    width: 1105px; height: 1200px; overflow: hidden;
    background: var(--backdrop);
    font-family: "Comic Neue", "Comic Sans MS", cursive;
    color: var(--ink);
  }
  .card {
    position: absolute; left: 196px; width: 720px; height: 412px;
    background: var(--card); border-radius: 26px; overflow: hidden;
  }
  .card--front { top: 146px; }
  .card--back { top: 602px; }

  .brand-name {
    position: absolute; top: 70px; left: 0; right: 0; text-align: center;
    font-size: 64px; font-weight: 400; letter-spacing: 2px;
  }
  .info-band {
    position: absolute; left: 0; right: 0; top: 216px; bottom: 0;
    background: var(--band); color: var(--on-band);
    border-radius: 28px 28px 0 0;
    font-size: 21px; line-height: 28px;
  }
  .contact { position: absolute; left: 36px; top: 26px; list-style: none; }
  .contact li { display: flex; align-items: center; gap: 8px; }
  .contact svg { width: 18px; height: 18px; fill: var(--on-band); }
  .offerings {
    position: absolute; right: 36px; top: 28px; list-style: none; text-align: right;
  }

  .card-number { position: absolute; top: 38px; right: 40px; font-size: 19px; }
  .backdrop-art {
    position: absolute; left: 232px; top: 33px; width: 325px; height: 352px;
    background: linear-gradient(180deg, var(--art-blue) 0%, var(--art-blue) 60%, var(--art-sun) 100%);
    opacity: 0.8; border-radius: 40% 40% 10% 10%;
  }
  .field { position: absolute; display: flex; align-items: flex-end; white-space: pre; }
  .field .label { font-weight: 700; }
  .field .fill-line { border-bottom: 1.5px solid var(--rule); height: 0; margin-bottom: 5px; }
  .field--major .label { font-size: 27px; }
  .field--minor .label { font-size: 22px; }
</style>
</head>
<body>
  <section class="card card--front" aria-label="Business card">
    <div class="brand-name">TILLOW MARSH</div>
    <div class="info-band">
      <ul class="contact">
        <li>482 Larkfield Ave.</li>
        <li>Harlow Bay, MI 48611</li>
        <li><svg viewBox="0 0 24 24" aria-hidden="true"><path d="M6.6 10.8a15.1 15.1 0 0 0 6.6 6.6l2.2-2.2a1 1 0 0 1 1-.25 11.4 11.4 0 0 0 3.6.57 1 1 0 0 1 1 1V20a1 1 0 0 1-1 1A17 17 0 0 1 3 4a1 1 0 0 1 1-1h3.5a1 1 0 0 1 1 1c0 1.25.2 2.45.57 3.57a1 1 0 0 1-.25 1z"/></svg>989.517.4296</li>
        <li><svg viewBox="0 0 24 24" aria-hidden="true"><path d="M2 5h20v14H2z M3 6l9 7 9-7" fill="var(--on-band)"/><path d="M3 6.5l9 6.5 9-6.5" stroke="#000" stroke-width="1.6" fill="none"/></svg>Office@TillowMarsh.com</li>
        <li><svg viewBox="0 0 24 24" aria-hidden="true"><circle cx="12" cy="12" r="10"/><path d="M7 7c2 0 3 1 3 3s-2 1-2 3 2 2 2 4M15 4c-1 2 0 3 2 3s2 2 1 4" stroke="#000" stroke-width="1.6" fill="none"/></svg>www.TillowMarsh.com</li>
      </ul>
      <ul class="offerings">
        <li>Gourmet Food</li>
        <li>Fine Wines</li>
        <li>Gift Baskets</li>
        <li>Kitchen &amp; Bath Accessories</li>
        <li>Candles | Cards | Soaps</li>
      </ul>
    </div>
  </section>

  <section class="card card--back" aria-label="Gift card back">
    <div class="backdrop-art" role="img" aria-label="Faint dancing figure with rising sun decoration"></div>
    <div class="card-number">Card Number : 58724</div>
    <div class="field field--major" style="left:58px; top:78px;"><span class="label">To :  </span><span class="fill-line" style="width:541px; margin-left:20px;"></span></div>
    <div class="field field--major" style="left:56px; top:136px;"><span class="label">Form : </span><span class="fill-line" style="width:515px; margin-left:6px;"></span></div>
    <div class="field field--minor" style="left:55px; top:222px;"><span class="label">Date  Issued :</span><span class="fill-line" style="width:473px; margin-left:4px;"></span></div>
    <div class="field field--minor" style="left:55px; top:270px;"><span class="label">Expiration Date :</span><span class="fill-line" style="width:443px; margin-left:4px;"></span></div>
    <div class="field field--minor" style="left:55px; top:319px;"><span class="label">Employee : </span><span class="fill-line" style="width:490px; margin-left:20px;"></span></div>
  </section>
</body>
</html>
```